Pennavault Web Design Project

We will need only one logo for Pennavault
Front Page
Header - Pennavault (logo) - Sites - Categories - Featured Contributors - Login (end header - the way markmaven does this is great, but I'm open to new ideas also)
(Start Page Content)
Pennavault (logo - centered)
weeklyoddments.com - thequickpost.com - stokingember.com (please leave spaces where we can place screenshots of those pages)
Sign Up!
Pennavault is a constantly growing network of sites that are dedicated to create relevant and well written content. If you are a student, professional, or a retiree, and you have an idea about a website that you would like to Contribute to, then this is the community that you have been looking for.
How It Works
Contribute An Article - Get Published - Increase Your Digital Footprint
Why We Exist
In the days when newspapers and radio stations dictated what the public read and heard, writers and editors were the gatekeepers in front of knowledge.
Those days are over and the lines between people who read content and publish content have become blurred. The outer-space like vastness of the internet is made larger exponentially every second by people who contribute data to it.
We believe that the future of knowledge in this world will have no gatekeepers and that every person is a contributor. This belief has lead to the creation of Pennavault.
Pennavault (logo-centered) - By The People, For The People
Footer
Follow Us: facebook, twitter, google+, youtube, instagram, linked in
____________________________
Categories Page (will need it's own page)
Arts & Entertainment - weeklyoddments.com
Health & Fitness - stokingember.com
News - thequickpost.com
If you’re interested in contributing to a topic listed below please email us at info@pennavault.com
Automotive
Business
Careers
Education
Family & Parenting
Personal Finance
Food & Drink
Hobbies & Interests
Home & Garden
Law, Government & Politics
Society
Science
Pets
Sports
Style & Fashion
Technology & Computing
Travel
Real Estate
Shopping
Religion and Spirituality
Uncategorized
___________________________
Sites Page (will need it's own page)
Weekly Oddments - weeklyoddments.com is an Arts & Entertainment website consisting of photo galleries and descriptions.
The Quickpost - thequickpost.com is a News website that is specifically dedicated to newly trending topics.
Stoking Ember - stokingember.com is a Health & Fitness website where visitors can find articles about workout routines, health supplements, and get ideas for eating clean.
_________________________
Featured Contributors Page (will need it's own page)
Content is to be determined
__________________________
NOTES FOR DESIGNER
We also will need a two column sub page that with one column being thin for navigation. We really like the simplicity of tidelume.com and markmaven.com. Those are two sites you can reference for the direcion we are heading in.
Thanks!
-Tommy
Updates
Hey Everyone!

```html
<!DOCTYPE html>
<html lang="en">
<head>
<meta charset="utf-8">
<title>Pennavault — By The People, For The People</title>
<link rel="stylesheet" href="https://fonts.googleapis.com/css2?family=Open+Sans:wght@300;400;600;700&display=swap">
<style>
  :root {
    --olive: #a4a234;
    --olive-dark: #7e7c1f;
    --olive-light: #c4c21a;
    --ink: #555555;
    --muted: #9a9a9a;
    --text-soft: #a8a8a8;
    --hero-bg: #e4e2c8;
    --panel: #f4f4f4;
    --white: #ffffff;
    --band: #9b9b9b;
  }
  * { margin: 0; padding: 0; box-sizing: border-box; }
  html, body { width: 769px; height: 1200px; overflow: hidden; }
  body { position: relative; font-family: "Open Sans", Arial, sans-serif; background: var(--panel); color: var(--ink); }
  .abs { position: absolute; }

  /* Header */
  .site-header { left: 0; top: 0; width: 769px; height: 60px; background: #f6f6f6; box-shadow: 0 1px 3px rgba(0,0,0,.08); z-index: 2; }
  .brand { font-weight: 700; color: var(--ink); font-size: 21px; letter-spacing: -.3px; }
  .site-header .brand { left: 64px; top: 14px; }
  .main-nav { left: 297px; top: 27px; display: flex; font-size: 9.5px; }
  .main-nav a { color: var(--ink); text-decoration: none; padding: 0 8px; border-left: 1px solid var(--ink); line-height: 12px; }
  .main-nav a:first-child { border-left: none; padding-left: 0; color: var(--olive); }
  .btn { display: block; background: var(--olive); color: var(--white); font-weight: 700; text-align: center; border-radius: 10px; border-bottom: 2px solid var(--olive-dark); text-decoration: none; }
  .btn-login { left: 583px; top: 23px; width: 57px; height: 22px; font-size: 10px; line-height: 20px; }
  .btn-signup-small { left: 648px; top: 23px; width: 57px; height: 22px; font-size: 10px; line-height: 20px; }

  /* Hero */
  .hero { left: 0; top: 60px; width: 769px; height: 324px; background: var(--hero-bg); }
  .site-card { width: 120px; text-align: center; }
  .site-card svg { display: block; margin: 0 auto; }
  .site-card span { display: block; margin-top: 8px; font-size: 9.5px; color: var(--olive); }
  .btn-signup-large { left: 336px; top: 251px; width: 96px; height: 37px; font-size: 15.5px; line-height: 34px; border-radius: 18px; border-bottom-width: 3px; }

  /* Intro */
  .intro { left: 0; top: 384px; width: 769px; height: 149px; background: linear-gradient(160deg, #ededed 0%, #fbfbfb 45%, #fafafa 100%); border-bottom: 1px solid #ececec; }
  .intro p { position: absolute; left: 120px; top: 47px; width: 528px; font-size: 10.4px; line-height: 19px; color: var(--text-soft); }

  /* How it works */
  .how { left: 0; top: 533px; width: 769px; height: 281px; background: var(--panel); }
  .section-title { width: 769px; text-align: center; font-weight: 300; }
  .how .section-title { top: 46px; font-size: 23.5px; color: var(--muted); letter-spacing: .5px; }
  .arrow { width: 40px; height: 42px; }
  .step { width: 170px; text-align: center; }
  .step-label { display: block; font-size: 15px; font-weight: 300; color: var(--olive); margin-top: 10px; white-space: nowrap; }
  .step-art { height: 90px; display: flex; align-items: flex-end; justify-content: center; }

  /* Why */
  .why { left: 0; top: 814px; width: 769px; height: 265px; background: var(--band); color: var(--white); }
  .why .section-title { top: 30px; font-size: 22.5px; color: var(--white); }
  .why-copy { left: 120px; top: 78px; width: 528px; font-size: 10.2px; line-height: 12.3px; text-align: justify; }
  .why .brand { width: 769px; top: 193px; text-align: center; color: var(--white); font-size: 21px; }
  .tagline { width: 769px; top: 223px; text-align: center; font-size: 10.5px; }

  /* Footer */
  .site-footer { left: 0; top: 1079px; width: 769px; height: 121px; background: var(--panel); text-align: center; }
  .follow { width: 769px; top: 12px; font-size: 11.5px; color: var(--muted); }
  .social { left: 306px; top: 36px; display: flex; gap: 6px; list-style: none; }
  .social li { width: 21px; height: 21px; border-radius: 3px; }
  .copyright { width: 769px; top: 96px; font-size: 7px; color: var(--text-soft); }
</style>
</head>
<body>

<header class="site-header abs">
  <div class="brand abs">Pennavault</div>
  <nav class="main-nav abs">
    <a href="#">Sites</a>
    <a href="#">Categories</a>
    <a href="#">Featured Contributors</a>
  </nav>
  <a class="btn btn-login abs" href="#">Login</a>
  <a class="btn btn-signup-small abs" href="#">Sign Up!</a>
</header>

<section class="hero abs">
  <div class="site-card abs" style="left:59px;top:60px;">
    <svg width="116" height="108" viewBox="0 0 116 108" role="img" aria-label="Screenshot of weeklyoddments.com">
      <polygon points="29,2 87,2 114,54 87,106 29,106 2,54" fill="#ffffff"/>
      <polygon points="32,7 84,7 108,54 84,101 32,101 8,54" fill="#e8c9b6"/>
    </svg>
    <span>weeklyoddments.com</span>
  </div>
  <div class="site-card abs" style="left:325px;top:60px;">
    <svg width="116" height="108" viewBox="0 0 116 108" role="img" aria-label="Screenshot of thequickpost.com">
      <polygon points="29,2 87,2 114,54 87,106 29,106 2,54" fill="#ffffff"/>
      <polygon points="32,7 84,7 108,54 84,101 32,101 8,54" fill="#c9bfb4"/>
    </svg>
    <span>thequickpost.com</span>
  </div>
  <div class="site-card abs" style="left:589px;top:60px;">
    <svg width="116" height="108" viewBox="0 0 116 108" role="img" aria-label="Screenshot of stokingember.com">
      <polygon points="29,2 87,2 114,54 87,106 29,106 2,54" fill="#ffffff"/>
      <polygon points="32,7 84,7 108,54 84,101 32,101 8,54" fill="#fbe9a0"/>
    </svg>
    <span>stokingember.com</span>
  </div>
  <a class="btn btn-signup-large abs" href="#">Sign Up!</a>
</section>

<section class="intro abs">
  <p>Pennavault is a constantly growing network of sites that are dedicated to create relevant and well written content. If you are a student, professional, or a retiree, and you have an idea about a website that you would like to Contribute to, then this is the community that you have been looking for.</p>
</section>

<section class="how abs">
  <h2 class="section-title abs">HOW IT WORKS</h2>

  <svg class="arrow abs" style="left:63px;top:117px;" viewBox="0 0 40 42" aria-label="Previous">
    <circle cx="20" cy="22" r="20" fill="var(--olive-light)"/>
    <circle cx="20" cy="20" r="20" fill="var(--olive)"/>
    <polyline points="23,14 17,20 23,26" fill="none" stroke="#fff" stroke-width="3.5" stroke-linecap="round" stroke-linejoin="round"/>
  </svg>
  <svg class="arrow abs" style="left:664px;top:117px;" viewBox="0 0 40 42" aria-label="Next">
    <circle cx="20" cy="22" r="20" fill="var(--olive-light)"/>
    <circle cx="20" cy="20" r="20" fill="var(--olive)"/>
    <polyline points="17,14 23,20 17,26" fill="none" stroke="#fff" stroke-width="3.5" stroke-linecap="round" stroke-linejoin="round"/>
  </svg>

  <div class="step abs" style="left:136px;top:105px;">
    <div class="step-art">
      <svg width="64" height="84" viewBox="0 0 64 84" aria-hidden="true">
        <path d="M0,0 H64 V74 L54,84 H0 Z" fill="var(--olive)"/>
        <path d="M54,84 L64,74 H54 Z" fill="#e6e6e6"/>
        <g stroke="#f4f4f4" stroke-width="3">
          <line x1="10" y1="16" x2="54" y2="16"/>
          <line x1="10" y1="26" x2="54" y2="26"/>
          <line x1="10" y1="36" x2="54" y2="36"/>
          <line x1="10" y1="46" x2="54" y2="46"/>
        </g>
      </svg>
    </div>
    <span class="step-label">Contribute An Article</span>
  </div>

  <div class="step abs" style="left:299px;top:105px;">
    <div class="step-art">
      <div role="img" aria-label="Megaphone illustration" style="width:76px;height:88px;border-radius:14px;background:linear-gradient(135deg,#dcdcd2 0%,#dcdcd2 50%,#8c8a2c 100%);"></div>
    </div>
    <span class="step-label">Get Published</span>
  </div>

  <div class="step abs" style="left:484px;top:105px;">
    <div class="step-art">
      <div role="img" aria-label="Footprints illustration" style="width:72px;height:95px;border-radius:20px;background:linear-gradient(160deg,#c4c21a 0%,#a4a234 100%);"></div>
    </div>
    <span class="step-label">Increase Your Digital Footprint</span>
  </div>
</section>

<section class="why abs">
  <h2 class="section-title abs">Why We Exist</h2>
  <div class="why-copy abs">
    <p>In the days when newspapers and radio stations dictated what the public read and heard, writers and editors were the gatekeepers in front of knowledge.</p>
    <p>Those days are over and the lines between people who read content and publish content have become blurred. The outer-space like vastness of the internet is made larger exponentially every second by people who contribute data to it.</p>
    <p>We believe that the future of knowledge in this world will have no gatekeepers and that every person is a contributor. This belief has lead to the creation of Pennavault.</p>
  </div>
  <div class="brand abs">Pennavault</div>
  <div class="tagline abs">By The People, For The People</div>
</section>

<footer class="site-footer abs">
  <div class="follow abs">Follow Us:</div>
  <ul class="social abs">
    <li style="background:#3b5a9a" role="img" aria-label="Social profile 1"></li>
    <li style="background:#4aa3d8" role="img" aria-label="Social profile 2"></li>
    <li style="background:#3a3a3a" role="img" aria-label="Social profile 3"></li>
    <li style="background:#b52a22" role="img" aria-label="Social profile 4"></li>
    <li style="background:#8a6a4c" role="img" aria-label="Social profile 5"></li>
    <li style="background:#2f7ab5" role="img" aria-label="Social profile 6"></li>
  </ul>
  <div class="copyright abs">© 2013 All Rights Reserved</div>
</footer>

</body>
</html>
```